Tech business card design

We need an amazing business card design for our new business 'Pexla' a marketing tech startup based in Sydney, Australia. We provide an online marketplace for businesses to search and buy advertising media, connect with service providers and learn more about marketing. We wish to communicate 'cool tech', reliability and professionalism and design based around our logo.

Target Market(s)

Business Owners

Contact Information for Business Card

Name
Position
Email Address
Website
Phone Number

Font styles to use
Other font styles liked:
• Avenir & Avenir Next

Colors

Designer to choose colors to be used in the design.

```html
<!DOCTYPE html>
<html lang="en">
<head>
<meta charset="utf-8">
<title>Pexla Business Card</title>
<link href="https://fonts.googleapis.com/css2?family=Lato:wght@400;700;900&display=swap" rel="stylesheet">
<style>
  :root {
    --backdrop: #2b2b2d;
    --card: #0e0e0f;
    --card-edge: #1a1a1b;
    --ink: #f2f2f2;
    --ink-soft: #cfcfcf;
    --divider: #8a8a8a;
  }
  * { margin: 0; padding: 0; box-sizing: border-box; }
  html, body {
    width: 1200px;
    height: 900px;
    overflow: hidden;
    background: var(--backdrop);
    font-family: "Lato", sans-serif;
  }
  .stage {
    position: relative;
    width: 1200px;
    height: 900px;
  }
  .card {
    position: absolute;
    left: 300px;
    width: 600px;
    height: 340px;
    background: linear-gradient(160deg, var(--card-edge), var(--card) 60%);
    border-radius: 3px;
    box-shadow: 0 18px 40px rgba(0,0,0,0.45);
  }
  .card--front { top: 70px; }
  .card--back { top: 490px; }

  .brand-name {
    position: absolute;
    left: 0; right: 0;
    top: 118px;
    text-align: center;
    font-weight: 900;
    font-size: 96px;
    line-height: 1;
    letter-spacing: -2px;
    color: var(--ink);
  }

  .contact-block {
    position: absolute;
    top: 124px;
    left: 0; right: 0;
    display: flex;
    justify-content: center;
    align-items: center;
    gap: 26px;
  }
  .person { text-align: right; }
  .person-name {
    font-weight: 700;
    font-size: 17px;
    letter-spacing: 0.5px;
    text-transform: uppercase;
    color: var(--ink);
  }
  .person-role {
    font-weight: 400;
    font-size: 15px;
    color: var(--ink-soft);
    margin-top: 2px;
  }
  .divider {
    width: 1px;
    height: 70px;
    background: var(--divider);
  }
  .details { list-style: none; }
  .details li {
    display: flex;
    align-items: center;
    gap: 8px;
    font-size: 15px;
    color: var(--ink-soft);
    line-height: 22px;
  }
  .details svg { width: 12px; height: 12px; fill: var(--ink-soft); }
</style>
</head>
<body>
  <main class="stage">
    <section class="card card--front">
      <p class="brand-name">pexla</p>
    </section>

    <section class="card card--back">
      <div class="contact-block">
        <div class="person">
          <p class="person-name">Daniel Hart</p>
          <p class="person-role">Managing Director</p>
        </div>
        <span class="divider"></span>
        <ul class="details">
          <li>
            <svg viewBox="0 0 12 12" aria-hidden="true"><path d="M1 4c0-2 2-3 5-3s5 1 5 3l-2 1-1-2H4L3 5zM2 6h8v5H2zm3 1v2h2V7z"/></svg>
            02-9000 4821
          </li>
          <li>
            <svg viewBox="0 0 12 12" aria-hidden="true"><path d="M1 2h10v8H1zm1 1v.5l4 3 4-3V3z"/></svg>
            info@pexlamail.com
          </li>
          <li>
            <svg viewBox="0 0 12 12" aria-hidden="true"><circle cx="6" cy="6" r="5"/><path d="M3 5l2-2 1 2-2 2zm4 2l2 1-2 2z" fill="#0e0e0f"/></svg>
            www.pexlamedia.com
          </li>
        </ul>
      </div>
    </section>
  </main>
</body>
</html>
```